Business card for law firm

Need business card for new law firm. Think confident, authoritative, conservative, but not stuffy or old-fashioned.

Contact Information for Business Card

Content for card - logo (uploaded), plus the following:

Paul Whitcombe (larger font)
Managing Partner (larger font, but not as large as name)
Level 9, 7 Ferris Lane
Sydney NSW 2000
Main Tel 02 9364 2710
Direct Tel 02 8472 3159
Email paul@qvlegal.com.au
www.qvlegal.com.au

Letterhead design should include logo plus:
Level 9, 7 Ferris Lane
Sydney NSW 2000
Tel 02 8472 3159
www.qvlegal.com.au

```html
<!DOCTYPE html>
<html lang="en">
<head>
<meta charset="utf-8">
<title>Quayvale Lawyers – Business Card</title>
<link rel="stylesheet" href="https://fonts.googleapis.com/css2?family=Cinzel:wght@500;600&family=Montserrat:wght@400;500&display=swap">
<style>
  :root {
    --backdrop: #2a2a2c;
    --card-black: #141416;
    --card-white: #ffffff;
    --navy: #1e2356;
    --ink: #1a1a1a;
    --deboss: #3b3b3f;
    --url-light: #e6e6e6;
  }
  * { margin: 0; padding: 0; box-sizing: border-box; }
  html, body {
    width: 1200px; height: 780px; overflow: hidden;
    background: var(--backdrop);
  }
  .canvas {
    width: 1200px; height: 780px;
    display: flex; align-items: center; justify-content: center; gap: 40px;
  }
  .card {
    width: 540px; height: 330px; position: relative; overflow: hidden;
  }

  /* Back face */
  .card--back {
    background: var(--card-black);
    display: flex; flex-direction: column; align-items: center; justify-content: center;
  }
  .back-mark {
    width: 46px; height: 46px; background: var(--deboss); margin-bottom: 18px;
  }
  .wordmark {
    font-family: "Cinzel", serif; font-weight: 500; text-align: center; line-height: 1;
  }
  .wordmark__name { font-size: 40px; letter-spacing: 1px; }
  .wordmark__sub { font-size: 11px; letter-spacing: 13px; margin-top: 6px; padding-left: 13px; }
  .card--back .wordmark { color: var(--deboss); }
  .back-url {
    font-family: "Montserrat", sans-serif; font-weight: 500; font-size: 13px;
    letter-spacing: 3px; color: var(--url-light); margin-top: 34px;
  }

  /* Front face */
  .card--front { background: var(--card-white); }
  .card--front .wordmark {
    position: absolute; left: 38px; top: 34px; color: var(--ink); text-align: center;
  }
  .card--front .wordmark__name { font-size: 34px; }
  .card--front .wordmark__sub { font-size: 9px; letter-spacing: 11px; padding-left: 11px; }
  .front-mark {
    position: absolute; right: 42px; top: 62px; width: 150px; height: 150px;
    background: var(--navy);
  }
  .person {
    position: absolute; left: 60px; top: 118px; color: var(--navy);
    font-family: "Montserrat", sans-serif;
  }
  .person__name {
    font-family: "Cinzel", serif; font-weight: 600; font-size: 20px; letter-spacing: 0.5px;
  }
  .person__role { font-size: 13px; margin-top: 1px; }
  .address { font-size: 13px; line-height: 1.4; margin-top: 12px; }
  .contacts { list-style: none; margin-top: 10px; font-size: 13px; }
  .contacts li { display: flex; align-items: center; gap: 10px; height: 18px; }
  .contacts svg { width: 11px; height: 11px; fill: var(--navy); flex: none; }
</style>
</head>
<body>
<main class="canvas">

  <section class="card card--back" aria-label="Card back">
    <div class="back-mark"></div>
    <div class="wordmark">
      <div class="wordmark__name">QUAYVALE</div>
      <div class="wordmark__sub">LAWYERS</div>
    </div>
    <div class="back-url">www.qvlegal.com.au</div>
  </section>

  <section class="card card--front" aria-label="Card front">
    <div class="wordmark">
      <div class="wordmark__name">QUAYVALE</div>
      <div class="wordmark__sub">LAWYERS</div>
    </div>
    <div class="front-mark"></div>

    <div class="person">
      <div class="person__name">PAUL WHITCOMBE</div>
      <div class="person__role">Managing Partner</div>
      <div class="address">Level 9, 7 Ferris Lane<br>Sydney NSW 2000</div>
      <ul class="contacts">
        <li>
          <svg viewBox="0 0 12 12" aria-hidden="true"><path d="M2.4 0.6 4.3 2.5 3.3 4c.6 1.6 2 3 3.7 3.7l1.5-1 1.9 1.9-1.2 1.9C5.5 10.4 1.6 6.5 0.5 1.8z"/></svg>
          <span>02 9364 2710</span>
        </li>
        <li>
          <svg viewBox="0 0 12 12" aria-hidden="true"><path d="M3 0h6a1 1 0 0 1 1 1v10a1 1 0 0 1-1 1H3a1 1 0 0 1-1-1V1a1 1 0 0 1 1-1zm.5 1.5v7.5h5V1.5zM6 9.8a.7.7 0 1 0 0 1.4.7.7 0 0 0 0-1.4z"/></svg>
          <span>02 8472 3159</span>
        </li>
        <li>
          <svg viewBox="0 0 12 12" aria-hidden="true"><path d="M0 2h12v8H0zm1.2 1.2v.3L6 6.6l4.8-3.1v-.3zm0 1.7v3.9h9.6V4.9L6 8z"/></svg>
          <span>paul@qvlegal.com.au</span>
        </li>
        <li>
          <svg viewBox="0 0 12 12" aria-hidden="true"><path d="M6 0a6 6 0 1 0 0 12A6 6 0 0 0 6 0zm0 1.2c.6.6 1.1 1.7 1.3 3.1H4.7C4.9 2.9 5.4 1.8 6 1.2zM4.6 5.5h2.8c0 .4 0 .7 0 1H4.6zm-1.2 0c0 .4 0 .7 0 1H1.3a4.8 4.8 0 0 1 0-1zm5.2 0h2.1a4.8 4.8 0 0 1 0 1H8.6zM4.7 7.7h2.6C7.1 9.1 6.6 10.2 6 10.8c-.6-.6-1.1-1.7-1.3-3.1zM3.5 4.3H1.7a4.8 4.8 0 0 1 2.6-2.6c-.4.7-.7 1.6-.8 2.6zm5 0c-.1-1-.4-1.9-.8-2.6a4.8 4.8 0 0 1 2.6 2.6zM1.7 7.7h1.8c.1 1 .4 1.9.8 2.6a4.8 4.8 0 0 1-2.6-2.6zm6.8 0h1.8a4.8 4.8 0 0 1-2.6 2.6c.4-.7.7-1.6.8-2.6z"/></svg>
          <span>www.qvlegal.com.au</span>
        </li>
      </ul>
    </div>
  </section>

</main>
</body>
</html>
```